Solar Company Bussiness Card

I need a 2 sided business card and would like a .psd and any font files for each side of the card. I would like my logo used, it should be attached with the fonts. I'm not opposed to the font colors with the logo being changed.

On the sample design, I'd like the following:

Marcus Dellow
President
Phone: 555-382-9174
www.brightvanepower.example

As I've recently opened in a 2nd market, I'm not sure about an address as I currently have 2 of them. I may actually get separate cards printed, one batch for each address, that's why I need the PSD file.
Updates

I'm very pleased with the response and designs I've received here for my business card. First and foremost, I'd like to thank everyone who took the time to submit a design. There truly are a lot of great designs in the bunch here and I'm having a little difficulty deciding. I will be reaching out to someone in the next day or two here to go to a final design. At this time, I'm not looking for any new concepts. If any of you do logos, I'm looking for a new logo for our sister entity, Dellow Partners, Inc. Thanks, Marcus Dellow

Reason: I'm not looking for any new designs at this point, but extending this deadline in order to give people I've asked a chance to re-submit items.

Industry/Entity Type

Business

```html
<!DOCTYPE html>
<html lang="en">
<head>
<meta charset="utf-8">
<title>Brightvane Power – Business Card</title>
<link rel="stylesheet" href="https://fonts.googleapis.com/css2?family=Noto+Sans:wght@400;500&display=swap">
<style>
  :root {
    --backdrop: #d8d8d4;
    --card: #ffffff;
    --card-edge: #e6e6e6;
    --brand-blue: #2b7cc4;
    --ink: #2f2f2f;
    --ink-soft: #444444;
    --shadow: rgba(0, 0, 0, 0.22);
  }
  * { box-sizing: border-box; margin: 0; padding: 0; }
  html, body {
    width: 1200px;
    height: 871px;
    overflow: hidden;
    background: var(--backdrop);
    font-family: "Noto Sans", Verdana, sans-serif;
  }
  .canvas {
    position: relative;
    width: 1200px;
    height: 871px;
  }
  .card {
    position: absolute;
    width: 590px;
    height: 337px;
    overflow: hidden;
    background: linear-gradient(160deg, var(--card) 55%, #f1f1f1 100%);
    border: 1px solid var(--card-edge);
    box-shadow: 0 10px 28px var(--shadow);
  }
  .card--front { left: 110px; top: 80px; }
  .card--back  { left: 500px; top: 450px; }

  .brand {
    display: flex;
    align-items: center;
    gap: 12px;
    color: var(--brand-blue);
    font-weight: 500;
    white-space: nowrap;
  }
  .brand__mark {
    background: var(--brand-blue);
    flex: none;
  }
  .card--front .brand {
    position: absolute;
    left: 50%;
    top: 50%;
    transform: translate(-50%, -50%);
    font-size: 42px;
  }
  .card--front .brand__mark { width: 40px; height: 40px; }

  .card--back .brand {
    position: absolute;
    left: 36px;
    top: 124px;
    font-size: 24px;
    gap: 8px;
  }
  .card--back .brand__mark { width: 23px; height: 23px; }

  .contact {
    position: absolute;
    left: 300px;
    top: 100px;
    width: 270px;
  }
  .contact__name {
    font-size: 19px;
    font-weight: 500;
    color: var(--ink);
    letter-spacing: 0.5px;
  }
  .contact__role {
    font-size: 14px;
    color: var(--brand-blue);
    margin-top: 1px;
    margin-bottom: 16px;
  }
  .contact__line {
    display: flex;
    align-items: center;
    gap: 12px;
    font-size: 14px;
    color: var(--ink-soft);
    letter-spacing: 0.5px;
    height: 28px;
    white-space: nowrap;
  }
  .contact__icon { width: 18px; height: 18px; flex: none; }
</style>
</head>
<body>
<main class="canvas">

  <section class="card card--front" aria-label="Card front">
    <div class="brand">
      <span class="brand__mark"></span>
      <span class="brand__name">Brightvane Power</span>
    </div>
  </section>

  <section class="card card--back" aria-label="Card back">
    <div class="brand">
      <span class="brand__mark"></span>
      <span class="brand__name">Brightvane Power</span>
    </div>

    <div class="contact">
      <p class="contact__name">Marcus Dellow</p>
      <p class="contact__role">President</p>

      <p class="contact__line">
        <svg class="contact__icon" viewBox="0 0 20 20" aria-hidden="true">
          <path d="M3 7 Q10 1 17 7 L15 9 L12.5 7.5 L12.5 6 Q10 5 7.5 6 L7.5 7.5 L5 9 Z" fill="var(--brand-blue)"/>
          <rect x="4" y="10" width="12" height="7" rx="1.5" fill="none" stroke="var(--brand-blue)" stroke-width="1.6"/>
          <circle cx="10" cy="13.5" r="1.6" fill="var(--brand-blue)"/>
        </svg>
        <span>555-382-9174</span>
      </p>

      <p class="contact__line">
        <svg class="contact__icon" viewBox="0 0 20 20" aria-hidden="true">
          <circle cx="10" cy="10" r="8" fill="none" stroke="var(--brand-blue)" stroke-width="1.6"/>
          <ellipse cx="10" cy="10" rx="3.5" ry="8" fill="none" stroke="var(--brand-blue)" stroke-width="1.4"/>
          <line x1="2" y1="10" x2="18" y2="10" stroke="var(--brand-blue)" stroke-width="1.4"/>
        </svg>
        <span>www.brightvanepower.example</span>
      </p>
    </div>
  </section>

</main>
</body>
</html>
```